Weightloss company needs Business Card

We want a business card that is clean and professional, yet portrays that we are a friendly, innovative, and versatile program designed to fit the needs of our clients.
I would like there to be 2 sides, one side having an appointment card, and the other side containing the logo and business information. There can be decorations on both sides. The logo is attached.

Target Market(s)

Men and women 40-60

Industry/Entity Type

Business

Contact Information for Business Card

Font styles to use
Sans Serif

Requirements
Must have
• The logo, space for business information
Nice to have
• The colors in the logo
Should not have
• No pictures of people or food

```html
<!DOCTYPE html>
<html lang="en">
<head>
<meta charset="utf-8">
<title>Pivotline Wellness – Business Card</title>
<link href="https://fonts.googleapis.com/css2?family=Open+Sans:wght@400;600;700;800&display=swap" rel="stylesheet">
<style>
  :root {
    --backdrop: #2e2e2e;
    --card-white: #ffffff;
    --card-black: #050505;
    --brand-red: #e3223a;
    --brand-blue: #4cc3ec;
    --faint-blue: #e6f5fc;
    --ink: #1c1c1c;
    --rule: #3a3a3a;
  }
  * { box-sizing: border-box; margin: 0; padding: 0; }
  html, body { width: 1200px; height: 900px; overflow: hidden; }
  body {
    background: var(--backdrop);
    font-family: "Open Sans", Arial, sans-serif;
    position: relative;
  }
  .card {
    position: absolute;
    width: 560px;
    height: 320px;
    border-radius: 22px;
    overflow: hidden;
    box-shadow: 0 18px 40px rgba(0,0,0,.45);
  }
  .brand-name {
    position: absolute;
    font-weight: 800;
    font-size: 30px;
    color: var(--brand-red);
    letter-spacing: .5px;
    line-height: 1;
    display: flex;
    align-items: center;
    gap: 10px;
  }
  .brand-dot {
    width: 16px; height: 16px; border-radius: 50%;
    background: var(--brand-blue);
  }

  /* Appointment side */
  .appointment-card { left: 70px; top: 90px; background: var(--card-white); }
  .appointment-card .brand-name { right: 36px; top: 40px; }
  .appointment-card .faint-circle {
    position: absolute; left: 150px; top: 90px;
    width: 200px; height: 200px; border-radius: 50%;
    background: var(--faint-blue);
  }
  .appointment-title {
    position: absolute; left: 44px; top: 140px;
    color: var(--brand-red); font-size: 15px; font-weight: 600; letter-spacing: .5px;
  }
  .appointment-field {
    position: absolute; left: 44px; right: 50px;
    display: flex; align-items: flex-end; gap: 10px;
    font-size: 15px; color: var(--ink);
  }
  .appointment-field .field-line { flex: 1; border-bottom: 1.5px solid var(--rule); height: 1px; margin-bottom: 4px; }
  .field-name { top: 172px; }
  .field-date { top: 218px; }
  .field-time { top: 264px; }

  /* Contact side */
  .contact-card { left: 570px; top: 480px; background: var(--card-white); }
  .contact-card .split { position: absolute; inset: 0; }
  .contact-card .brand-name { right: 36px; top: 50px; }
  .contact-card .big-circle {
    position: absolute; left: 34px; top: 200px;
    width: 96px; height: 96px; border-radius: 50%;
    background: var(--brand-blue);
  }
  .person {
    position: absolute; right: 36px; top: 138px; text-align: right;
  }
  .person-name { color: #fff; font-size: 20px; letter-spacing: .5px; }
  .person-role { color: var(--brand-blue); font-size: 12px; font-weight: 600; letter-spacing: .8px; }
  .contact-list {
    position: absolute; left: 160px; top: 244px;
    list-style: none; font-size: 13px; color: var(--ink); line-height: 21px;
  }
  .contact-list li { display: flex; align-items: center; gap: 8px; }
  .contact-list svg { width: 12px; height: 12px; }
  .address {
    position: absolute; right: 30px; top: 244px; text-align: right;
    font-size: 13px; color: var(--ink); line-height: 21px;
  }
</style>
</head>
<body>

<section class="card appointment-card">
  <div class="faint-circle"></div>
  <div class="brand-name">Pivotline Wellness<span class="brand-dot"></span></div>
  <p class="appointment-title">APPOINTMENT</p>
  <div class="appointment-field field-name"><span>Name:</span><span class="field-line"></span></div>
  <div class="appointment-field field-date"><span>Date:</span><span class="field-line"></span></div>
  <div class="appointment-field field-time"><span>Time:</span><span class="field-line"></span></div>
</section>

<section class="card contact-card">
  <svg class="split" viewBox="0 0 560 320" preserveAspectRatio="none" aria-hidden="true">
    <polygon points="0,0 560,0 560,190 0,262" fill="var(--card-black)"/>
    <line x1="0" y1="262" x2="560" y2="190" stroke="var(--brand-red)" stroke-width="4"/>
  </svg>
  <div class="brand-name">Pivotline Wellness<span class="brand-dot"></span></div>
  <div class="person">
    <p class="person-name">MARCUS HALE</p>
    <p class="person-role">DIRECTOR</p>
  </div>
  <div class="big-circle"></div>
  <ul class="contact-list">
    <li><svg viewBox="0 0 12 12"><path d="M2 1l2 0 1 3-1.5 1a6 6 0 0 0 3 3L7.5 6.5l3 1v2a1 1 0 0 1-1 1A9 9 0 0 1 1 2a1 1 0 0 1 1-1z" fill="var(--brand-red)"/></svg>+100 5550-1234</li>
    <li><svg viewBox="0 0 12 12"><rect x="1" y="2.5" width="10" height="7" fill="none" stroke="var(--brand-red)" stroke-width="1.2"/><path d="M1 2.5l5 4 5-4" fill="none" stroke="var(--brand-red)" stroke-width="1.2"/></svg>info@pivotlinewellness.com</li>
    <li><svg viewBox="0 0 12 12"><circle cx="6" cy="6" r="5" fill="none" stroke="var(--brand-red)" stroke-width="1.2"/><path d="M1 6h10M6 1c-2.5 3-2.5 7 0 10M6 1c2.5 3 2.5 7 0 10" fill="none" stroke="var(--brand-red)" stroke-width="1"/></svg>www.pivotlinewellness.com</li>
  </ul>
  <address class="address" style="font-style:normal">Harbor Lane, 40210<br>Easton, Northland</address>
</section>

</body>
</html>
```